Zvo Klinieken website for a maxillofacial surgery clinic

It's a website for a clinic for maxillofacial surgery in WordPress . The website doesn't need to be complicated but has to look professional. It needs to be in Dutch so i can give the texts. Similar websites are www.tandartsenpraktijkveldorm.nl or www.pbtspecialisten.nl. Pages would be sort of similar to https://hetcentrumvoorgezichtszorg.nl/ or https://wervelmondclinics.nl/. Those lasts are maxillofacial surgery clinic websites, but there are little more extensive.
I uploaded the logo. If this is not the proper quality i can upload the eps. Logo was made through pixelforum.

Target Market(s)

Patients who can find me and see information about the clinic

Industry/Entity Type

Healthcare

Coding

Coded - Design and coding required

Number of Pages Required

5+ page

Font styles to use
Other font styles liked:
• Something standard professional

Colors
0054AA
0677BA
7BADD7
CADEEF
E8F1F8

Requirements
Nice to have
• Something in line with the logo. I prefer a little dark like the darker logos but I'm not sure if that's professional. Logos bkvzo and rlpw are instances i'm registered to so they will have to be on the website too but small somewhere.

```html
<!DOCTYPE html>
<html lang="nl">
<head>
<meta charset="utf-8">
<title>Zvo Klinieken Zoetermeer</title>
<link href="https://fonts.googleapis.com/css2?family=Open+Sans:wght@400;600&display=swap" rel="stylesheet">
<style>
:root{
  --sky:#2ba4e0;
  --sky-soft:#55b9e8;
  --sky-pale:#c9e8f9;
  --slate:#6a7d9e;
  --ink:#111;
  --text:#333;
  --card:#f5f5f5;
  --footer:#161616;
  --white:#fff;
}
*{box-sizing:border-box;margin:0;padding:0}
html,body{width:1200px;height:3109px;overflow:hidden}
body{font-family:Arial,Helvetica,sans-serif;color:var(--text);background:var(--white);position:relative}
.heading{font-family:"Open Sans",Arial,sans-serif;font-weight:400}
section,header,footer{position:relative;width:1200px;overflow:hidden}

/* header */
.site-header{height:109px}
.topbar{position:absolute;left:340px;top:0;right:0;height:33px;background:var(--slate);clip-path:polygon(0 0,100% 0,100% 100%,18px 100%);color:#fff;font-size:14px;display:flex;justify-content:flex-end;gap:36px;align-items:center;padding-right:112px}
.topbar span{display:flex;align-items:center;gap:8px}
.brand{position:absolute;left:114px;top:22px;display:flex;align-items:center;gap:10px;font-family:"Open Sans",sans-serif;font-weight:600;font-size:26px;color:var(--sky)}
.brand i{width:22px;height:22px;border-radius:50%;background:var(--sky);display:block}
.nav{position:absolute;right:114px;top:66px;display:flex;gap:34px;font-size:15px;color:#222}

/* hero */
.hero{height:428px;background:var(--sky)}
.hero-ring{position:absolute;left:559px;top:-21px;width:536px;height:536px;border-radius:50%;background:var(--sky-soft)}
.hero-photo{position:absolute;left:631px;top:40px;width:460px;height:388px;border-radius:230px 230px 0 0;background:linear-gradient(180deg,#aee0f6,#dfeef7)}
.hero h1{position:absolute;left:112px;top:122px;color:#fff;font-size:58px;line-height:66px}
.btn{display:inline-block;font-family:"Open Sans",sans-serif;font-weight:600;color:#fff;font-size:15px;border-radius:5px;text-align:center}
.hero .btn{position:absolute;left:112px;top:286px;width:218px;height:50px;line-height:50px;background:var(--slate)}
.arrow{position:absolute;top:193px;width:42px;height:42px}

/* about */
.about{height:592px}
.about-frame{position:absolute;left:130px;top:82px;width:330px;height:430px;border:1.5px solid #d9dde3;border-radius:6px}
.about-photo{position:absolute;left:112px;top:68px;width:328px;height:427px;border-radius:4px;background:linear-gradient(160deg,#b88a4c,#e9d6b8);box-shadow:0 8px 18px rgba(0,0,0,.18)}
.about h2{position:absolute;left:531px;top:68px;font-size:44px;color:var(--ink)}
.about .lead{position:absolute;left:531px;top:142px;width:560px;font-size:15px;font-weight:bold;line-height:28px;color:#111}
.about .body{position:absolute;left:531px;top:210px;width:560px;font-size:15px;line-height:28.5px}
.quote{position:absolute;left:525px;top:381px;width:561px;height:109px;background:var(--sky-pale);border-radius:4px;padding:22px 40px;font-size:19px;line-height:33px;color:#222}

/* surgery */
.surgery{height:435px;background:var(--slate)}
.surgery-photo{position:absolute;left:560px;top:0;width:640px;height:435px;background:linear-gradient(90deg,var(--slate) 0%,#a9b6c8 45%,#d9dee6 100%)}
.surgery h2{position:absolute;left:111px;top:68px;color:#fff;font-size:44px}
.surgery p{position:absolute;left:111px;top:150px;width:520px;color:#fff;font-size:15px;line-height:28.5px}
.surgery .btn{position:absolute;left:111px;top:324px;width:210px;height:51px;line-height:51px;background:var(--sky)}

/* why */
.why{height:672px}
.why h2{position:absolute;left:0;right:0;top:68px;text-align:center;font-size:44px;color:var(--ink)}
.card{position:absolute;width:234px;height:371px;background:var(--card);border-radius:5px;text-align:center;padding:32px 16px 0}
.card svg{display:block;margin:0 auto 18px}
.card h3{font-family:"Open Sans",sans-serif;font-weight:600;font-size:16px;line-height:29px;color:#111;margin-bottom:18px}
.card p{font-family:"Open Sans",sans-serif;font-size:16px;line-height:28.5px;color:#444}

/* appointment */
.appointment{height:497px;background:var(--sky)}
.appointment h2{position:absolute;left:0;right:0;top:48px;text-align:center;font-size:44px;color:#fff}
.stripes{position:absolute;left:221px;top:314px;width:157px;height:153px;background:#3aaee5}
.field{position:absolute;background:#fff;height:49px;font-size:15px;color:#555;padding:16px 16px}
.field.message{height:97px}
.appointment .btn{position:absolute;left:542px;top:385px;width:116px;height:50px;line-height:50px;background:var(--slate)}

/* footer */
.site-footer{height:376px;background:var(--footer);color:#fff}
.footer-brand{position:absolute;left:112px;top:128px;display:flex;align-items:center;gap:12px;font-family:"Open Sans",sans-serif;font-weight:600;font-size:34px;color:var(--sky)}
.footer-brand i{width:30px;height:30px;border-radius:50%;background:var(--sky);display:block}
.col{position:absolute;top:104px}
.col h4{font-family:"Open Sans",sans-serif;font-weight:400;font-size:16px;letter-spacing:.3px}
.col h4:after{content:"";display:block;width:38px;height:2px;background:var(--sky);margin-top:9px}
.col ul{list-style:none;margin-top:14px;font-size:15px;line-height:26px}
.col ul li:before{content:"›";margin-right:7px;font-weight:bold}
.contact-list{margin-top:14px;font-size:13.5px}
.contact-list div{display:flex;gap:14px;line-height:26px;margin-bottom:6px}
.contact-list svg{flex:none;margin-top:6px}
.divider{position:absolute;left:112px;right:112px;top:311px;height:1px;background:#333}
.copyright{position:absolute;left:415px;top:338px;font-size:14px}
</style>
</head>
<body>

<header class="site-header">
  <div class="topbar">
    <span><svg width="12" height="10" viewBox="0 0 12 10"><rect x="0" y="1" width="12" height="8" fill="#fff"/><path d="M0 1l6 5 6-5" stroke="#6a7d9e" fill="none"/></svg>+31 79 555 0142</span>
    <span><svg width="10" height="10" viewBox="0 0 10 10"><path d="M2 0l2 2-1 2c1 1 2 2 3 3l2-1 2 2-2 2C4 10 0 6 0 2z" fill="#fff"/></svg>info@zvoklinieken.nl</span>
  </div>
  <div class="brand"><i></i>Zvo Klinieken</div>
  <nav class="nav"><span>Home</span><span>Over</span><span>Chirurgie</span><span>Kwaliteit</span><span>Veelgestelde vragen</span><span>Doorverwijzers</span><span>Contact</span></nav>
</header>

<section class="hero">
  <div class="hero-ring"></div>
  <div class="hero-photo" role="img" aria-label="Foto van twee glimlachende artsen in witte jas en blauw uniform"></div>
  <h1 class="heading">Maxillofacial<br>Chirurgie Kliniek</h1>
  <span class="btn">MEER TE WETEN KOMEN</span>
  <svg class="arrow" style="left:37px" viewBox="0 0 42 42"><circle cx="21" cy="21" r="19" fill="none" stroke="#7ecbee" stroke-width="3"/><path d="M24 13l-8 8 8 8" fill="none" stroke="#7ecbee" stroke-width="3"/></svg>
  <svg class="arrow" style="left:1127px" viewBox="0 0 42 42"><circle cx="21" cy="21" r="19" fill="none" stroke="#fff" stroke-width="3"/><path d="M18 13l8 8-8 8" fill="none" stroke="#fff" stroke-width="3"/></svg>
</section>

<section class="about">
  <div class="about-frame"></div>
  <div class="about-photo" role="img" aria-label="Portretfoto van een lachende vrouw met krullend haar"></div>
  <h2 class="heading">Over ons</h2>
  <p class="lead">Lorem ipsum dolor sit amet, consectetur adipiscing elit, sed do eiusmod tempor incididunt ut . Ut enim ad minim veniam, quis nostrud exercit.</p>
  <p class="body">Sed ut perspiciatis unde omnis iste natus error sit voluptatem accusantium dolor emque laudantium, totam rem aperiam, eaque ipsa quae ab illo inventore verita tis et quasi architecto beatae vitae dicta sunt explicabo. Nemo enim ipsam vo luptatem quia voluptas sit aspernatur aut odit aut fugit, sed quia consequuntur magni dolores eos qui ratione voluptatem sequi nesciunt.</p>
  <div class="quote">Neque porro quisquam est, qui dolorem ipsum quia dolor sit amet, consectetur, adipisci velit, sed quinon numquam.</div>
</section>

<section class="surgery">
  <div class="surgery-photo" role="img" aria-label="Foto van een arts die een röntgenfoto van het gebit uitlegt aan een patiënt"></div>
  <h2 class="heading">Maxillofaciale chirurgie</h2>
  <p>Sed ut perspiciatis unde omnis iste natus error sit voluptatem accuntium doloremque laudantium, totam rem aperiam, eaque ipsa qub illo inventore veritatis et quasi architecto beatae vitae dicta sunt ebo. Nemo enim ipsam voluptatem quia voluptas sit aspernatur aut oditgt, sed quia consequuntur magni dolores eos qui ratione voluptatem ssciunt.</p>
  <span class="btn">KOM MEER TE WETEN</span>
</section>

<section class="why">
  <h2 class="heading">Waarom voor ons kiezen</h2>
  <div class="card" style="left:110px;top:175px">
    <svg width="66" height="66" viewBox="0 0 66 66"><circle cx="33" cy="33" r="31" fill="#cfe9f8"/><circle cx="33" cy="33" r="30" fill="none" stroke="#222" stroke-width="2"/><path d="M22 22c4-4 8-1 11-1s7-3 11 1c3 4 0 12-2 20-1 4-4 4-5 0l-2-7c-1-3-3-3-4 0l-2 7c-1 4-4 4-5 0-2-8-5-16-2-20z" fill="#fff" stroke="#222" stroke-width="2"/></svg>
    <h3>Lorem ipsum dolor<br>sit amet consectetur.</h3>
    <p>Nam libero tempore, cum soluta noest eligendi optio cumque nihil impedit quo mi id quod maxime placeat facere possimus.</p>
  </div>
  <div class="card" style="left:358px;top:209px">
    <svg width="66" height="66" viewBox="0 0 66 66"><circle cx="38" cy="36" r="22" fill="#cfe9f8"/><circle cx="33" cy="30" r="22" fill="none" stroke="#222" stroke-width="2"/><path d="M26 24c0-5 4-8 8-8s8 3 8 7c0 5-8 6-8 11" fill="none" stroke="#222" stroke-width="2.5"/><circle cx="34" cy="41" r="2" fill="#222"/><circle cx="12" cy="58" r="3" fill="none" stroke="#222" stroke-width="2"/></svg>
    <h3>Lorem ipsum dolor<br>sit amet consectetur.</h3>
    <p>Nam libero tempore, cum soluta noest eligendi optio cumque nihil impedit quo mi id quod maxime placeat facere possimus.</p>
  </div>
  <div class="card" style="left:607px;top:175px">
    <svg width="66" height="66" viewBox="0 0 66 66"><circle cx="33" cy="28" r="18" fill="#cfe9f8" stroke="#222" stroke-width="2"/><path d="M33 12v32M26 20c-4 2-4 8 0 10M40 20c4 2 4 8 0 10" fill="none" stroke="#222" stroke-width="2"/><rect x="26" y="46" width="14" height="10" rx="2" fill="none" stroke="#222" stroke-width="2"/><path d="M6 28h5M55 28h5M12 10l4 4M54 10l-4 4" stroke="#222" stroke-width="2"/></svg>
    <h3>Lorem ipsum dolor<br>sit amet consectetur.</h3>
    <p>Nam libero tempore, cum soluta noest eligendi optio cumque nihil impedit quo mi id quod maxime placeat facere possimus.</p>
  </div>
  <div class="card" style="left:856px;top:209px">
    <svg width="66" height="66" viewBox="0 0 66 66"><circle cx="40" cy="38" r="20" fill="#cfe9f8"/><circle cx="40" cy="16" r="10" fill="#fff" stroke="#222" stroke-width="2"/><path d="M40 10v12M34 16h12" stroke="#222" stroke-width="2.5"/><path d="M34 28L14 52l-4 4 4-1 24-22z" fill="#fff" stroke="#222" stroke-width="2"/></svg>
    <h3>Lorem ipsum dolor<br>sit amet consectetur.</h3>
    <p>Nam libero tempore, cum soluta noest eligendi optio cumque nihil impedit quo mi id quod maxime placeat facere possimus.</p>
  </div>
</section>

<section class="appointment">
  <h2 class="heading">Afspraak Aanvragen</h2>
  <div class="stripes" role="img" aria-label="Decoratief streepjespatroon"></div>
  <div class="field" style="left:270px;top:149px;width:325px">Naam:</div>
  <div class="field" style="left:605px;top:149px;width:325px">Leeftijd:</div>
  <div class="field" style="left:270px;top:208px;width:325px">E-mail:</div>
  <div class="field" style="left:605px;top:208px;width:325px">Telefoon:</div>
  <div class="field message" style="left:270px;top:267px;width:660px">Message:</div>
  <span class="btn">INDIENEN</span>
</section>

<footer class="site-footer">
  <div class="footer-brand"><i></i>Zvo Klinieken</div>
  <div class="col" style="left:415px">
    <h4>CONTACT</h4>
    <div class="contact-list">
      <div><svg width="14" height="16" viewBox="0 0 14 16"><path d="M7 0a6 6 0 0 0-6 6c0 4 6 10 6 10s6-6 6-10a6 6 0 0 0-6-6z" fill="#2ba4e0"/><circle cx="7" cy="6" r="2.2" fill="#161616"/></svg><span>Zvo Klinieken Zoetermeer,<br>Adres komt hier</span></div>
      <div><svg width="15" height="15" viewBox="0 0 10 10"><path d="M2 0l2 2-1 2c1 1 2 2 3 3l2-1 2 2-2 2C4 10 0 6 0 2z" fill="#2ba4e0"/></svg><span>+31 79 555 0140</span></div>
      <div><svg width="15" height="12" viewBox="0 0 12 10"><rect x="0" y="1" width="12" height="8" fill="#2ba4e0"/><path d="M0 1l6 5 6-5" stroke="#161616" fill="none"/></svg><span>info@zvoklinieken.nl</span></div>
    </div>
  </div>
  <div class="col" style="left:731px">
    <h4>QUICK LINKS</h4>
    <ul><li>Home</li><li>Over</li><li>Chirurgie</li><li>Kwaliteit</li></ul>
  </div>
  <div class="col" style="left:935px">
    <h4>OTHER LINKS</h4>
    <ul><li>Veelgestelde vragen</li><li>Doorverwijzers</li><li>Contact</li></ul>
  </div>
  <div class="divider"></div>
  <p class="copyright">2023 Zvo Klinieken Zoetermeer. Alle rechten voorbehouden.</p>
</footer>

</body>
</html>
```